Health and wellnes company needs business cards

We are a Health and wellness business just relocated to Spain. Here nobody knows our business so we would like to put some of our services on the card. Clean design with logo.

Contact Information for Business Card

Brightmeadow
Paula & Oskar Dunbeck
Calle del Almendro 57
Villamar de la Costa
Mobile: 0046 731 402687
info@brightmeadow.example

Font styles to use
Serif

Colors
85cae6
85acd3
b768aa

Requirements
Must have
• these Services somewhere on the card
• - Private or group yoga
• - Reconnective healing
• - Kitesurfing lessons
• - Massage
• LOgo somewhere
Nice to have
• Colours that go with the logo please

```html
<!DOCTYPE html>
<html lang="en">
<head>
<meta charset="utf-8">
<title>Brightmeadow business card</title>
<link rel="stylesheet" href="https://fonts.googleapis.com/css2?family=Marcellus&family=Alegreya:wght@500&family=Varela+Round&family=Roboto:wght@400&display=swap">
<style>
  :root {
    --navy: #1e3d6b;
    --navy-top: #26476f;
    --navy-bottom: #173562;
    --teal: #6cc5c9;
    --text-grey: #555a60;
    --rule-grey: #c9cdd2;
    --paper: #ffffff;
    --backdrop: #e6e6e6;
  }
  * { margin: 0; padding: 0; box-sizing: border-box; }
  html, body { width: 1200px; height: 1200px; overflow: hidden; }
  body { background: var(--backdrop); position: relative; }

  .card {
    position: absolute;
    left: 200px;
    width: 800px;
    height: 457px;
  }
  .card-front { top: 110px; background: var(--paper); }
  .card-back {
    top: 680px;
    background: linear-gradient(180deg, var(--navy-top), var(--navy-bottom));
  }

  /* front */
  .brand {
    position: absolute;
    left: 110px;
    top: 155px;
    width: 270px;
    text-align: center;
  }
  .brand-ring {
    display: block;
    margin: 0 auto 14px;
  }
  .brand-name {
    font-family: "Marcellus", serif;
    font-size: 27px;
    color: var(--navy);
    letter-spacing: 0.3px;
    line-height: 1;
    white-space: nowrap;
  }
  .divider {
    position: absolute;
    width: 1px;
    background: linear-gradient(180deg, transparent, var(--rule-grey) 15%, var(--rule-grey) 85%, transparent);
  }
  .card-front .divider { left: 399px; top: 130px; height: 200px; }
  .contact {
    position: absolute;
    left: 433px;
    top: 143px;
  }
  .contact-names {
    font-family: "Alegreya", serif;
    font-weight: 500;
    font-size: 21px;
    color: var(--navy);
    line-height: 1;
  }
  .contact-names .second { color: var(--teal); }
  .address, .channels {
    font-family: "Varela Round", sans-serif;
    font-size: 18px;
    color: var(--text-grey);
    line-height: 22px;
  }
  .address { margin-top: 16px; }
  .channels { margin-top: 16px; list-style: none; }
  .channels li { display: flex; align-items: center; gap: 9px; margin-left: 1px; }
  .channels svg { flex: none; width: 15px; height: 15px; fill: var(--navy); }

  /* back */
  .back-brand {
    position: absolute;
    left: 200px;
    top: 163px;
    width: 140px;
    text-align: center;
  }
  .back-brand .brand-name { color: var(--paper); font-size: 15px; }
  .back-brand .brand-ring { margin-bottom: 10px; }
  .card-back .divider {
    left: 368px; top: 155px; height: 145px;
    background: linear-gradient(180deg, transparent, rgba(255,255,255,0.35) 15%, rgba(255,255,255,0.35) 85%, transparent);
  }
  .services {
    position: absolute;
    left: 396px;
    top: 180px;
    list-style: none;
    font-family: "Roboto", sans-serif;
    font-size: 19px;
    line-height: 22.5px;
    color: var(--paper);
  }
  .services li { position: relative; padding-left: 15px; }
  .services li::before {
    content: "";
    position: absolute;
    left: 0; top: 9px;
    width: 6px; height: 6px;
    border-radius: 50%;
    background: var(--teal);
  }
</style>
</head>
<body>

<section class="card card-front">
  <div class="brand">
    <svg class="brand-ring" width="100" height="100" viewBox="0 0 100 100" aria-hidden="true">
      <circle cx="50" cy="50" r="45" fill="none" stroke="var(--teal)" stroke-width="7"/>
    </svg>
    <div class="brand-name">BRIGHTMEADOW</div>
  </div>

  <div class="divider"></div>

  <div class="contact">
    <p class="contact-names">Paula &amp; <span class="second">Oskar Dunbeck</span></p>
    <p class="address">Calle del Almendro 57<br>Villamar de la Costa</p>
    <ul class="channels">
      <li>
        <svg viewBox="0 0 16 16" aria-hidden="true"><path d="M4 0h8a1.5 1.5 0 0 1 1.5 1.5v13A1.5 1.5 0 0 1 12 16H4a1.5 1.5 0 0 1-1.5-1.5v-13A1.5 1.5 0 0 1 4 0zm0.2 2v10.5h7.6V2zM8 13.3a0.9 0.9 0 1 0 0 1.8a0.9 0.9 0 0 0 0-1.8z"/></svg>
        0046 731 402687
      </li>
      <li>
        <svg viewBox="0 0 16 16" aria-hidden="true"><path d="M1 4h14v1L8 9.5L1 5zm0 2.4l7 4.5l7-4.5V13H1z"/></svg>
        info@brightmeadow.example
      </li>
      <li>
        <svg viewBox="0 0 16 16" aria-hidden="true"><path d="M8 0.5a7.5 7.5 0 1 0 0 15a7.5 7.5 0 0 0 0-15zm-1 2.2c0.8 0.6 0.3 1.6-0.6 2s-1.6 1.4-0.7 2.1s2.2 0.2 2.5 1.4s-0.9 1.8-0.5 3.1s-0.6 2-1.3 1.1S5.8 10 4.8 9.5S2.6 7.4 3 5.6s2.6-3.5 4-2.9zm4.4 1.5c1.2 0.8 2 2.2 2.1 3.8c-0.9-0.1-1.8-0.8-2.2-1.8s-0.6-1.4 0.1-2z"/></svg>
        www.brightmeadow.example
      </li>
    </ul>
  </div>
</section>

<section class="card card-back">
  <div class="back-brand">
    <svg class="brand-ring" width="110" height="110" viewBox="0 0 110 110" aria-hidden="true">
      <circle cx="55" cy="55" r="50" fill="none" stroke="var(--teal)" stroke-width="7"/>
    </svg>
    <div class="brand-name">BRIGHTMEADOW</div>
  </div>

  <div class="divider"></div>

  <ul class="services">
    <li>Private or group yoga</li>
    <li>Reconnective healing</li>
    <li>Kitesurfing lessons</li>
    <li>Massage</li>
  </ul>
</section>

</body>
</html>
```